Kestrelbrook Student Accomodation needs a business card design

Hi Guys,

We are a Student Accommodation company in Australia. We already have a logo which I will submit.

I will require the design of the business cards from you.

I am after something that looks clean, modern and that people feel interested and actually want to contact us.

We would like to see designs that are innovative.

On the business cards I will require to have:

Employee Name
Position
Phone number
Email
Facebook page

I hope you can help me with this project guys as I have heard really good things from you.

```html
<!DOCTYPE html>
<html lang="en">
<head>
<meta charset="utf-8">
<title>Kestrelbrook Student Accomodation – Business Card</title>
<link rel="stylesheet" href="https://fonts.googleapis.com/css2?family=Open+Sans:wght@400;600;700&display=swap">
<style>
  :root {
    --stage: #e4e5e6;
    --card-white: #ffffff;
    --brand-green: #0b9140;
    --brand-yellow: #f4b638;
    --brand-orange: #e9a11d;
    --ink: #1e1e1e;
    --on-green: #ffffff;
  }
  * { box-sizing: border-box; margin: 0; padding: 0; }
  html, body {
    width: 1200px; height: 680px; overflow: hidden;
    background: var(--stage);
    font-family: "Open Sans", Verdana, sans-serif;
  }
  .canvas {
    position: relative; width: 1200px; height: 680px;
    display: flex; align-items: center; justify-content: center; gap: 60px;
  }
  .card {
    position: relative; width: 520px; height: 300px;
    border-radius: 22px; overflow: hidden;
    box-shadow: 0 6px 18px rgba(0,0,0,.14);
  }

  /* Front */
  .card--front { background: var(--card-white); color: var(--ink); }
  .card__swoosh { position: absolute; inset: 0; width: 100%; height: 100%; }
  .brand {
    position: absolute; left: 40px; top: 112px;
    display: flex; align-items: center; gap: 14px;
  }
  .brand__mark { width: 44px; height: 44px; background: var(--brand-yellow); flex: none; }
  .brand__name {
    font-weight: 700; font-size: 17px; line-height: 1.2;
    color: var(--brand-green); width: 190px;
  }
  .person { position: absolute; right: 44px; top: 98px; text-align: left; }
  .person__name { font-size: 17px; letter-spacing: .5px; }
  .person__role { font-size: 13px; color: var(--brand-green); margin-left: 70px; }
  .phone {
    position: absolute; right: 44px; top: 164px;
    display: flex; align-items: center; gap: 8px; font-size: 15px; letter-spacing: .5px;
  }
  .contacts { position: absolute; left: 40px; bottom: 30px; font-size: 15px; line-height: 1.35; }
  .contacts__row { display: flex; align-items: center; gap: 8px; }
  .icon { width: 14px; height: 14px; flex: none; }

  /* Back */
  .card--back { background: var(--brand-green); color: var(--on-green); }
  .card--back .brand { left: 100px; top: 96px; }
  .card--back .brand__name { color: var(--on-green); font-size: 22px; width: 250px; }
  .card--back .brand__mark { width: 56px; height: 56px; }
  .web { position: absolute; right: 40px; bottom: 34px; font-size: 16px; letter-spacing: .3px; }
</style>
</head>
<body>
<main class="canvas">

  <section class="card card--front" aria-label="Business card front">
    <svg class="card__swoosh" viewBox="0 0 520 300" aria-hidden="true">
      <path d="M150 0 C 270 6, 420 30, 520 92 L 520 100 C 420 44, 270 18, 150 0 Z" fill="var(--brand-orange)"/>
      <path d="M190 0 L 520 0 L 520 62 C 430 26, 310 8, 190 0 Z" fill="var(--card-white)"/>
      <path d="M250 0 C 360 6, 460 26, 520 56 L 520 70 C 450 36, 350 14, 250 0 Z" fill="var(--brand-yellow)"/>
      <path d="M340 0 C 420 4, 480 14, 520 28 L 520 36 C 470 20, 410 8, 340 0 Z" fill="var(--brand-orange)"/>
    </svg>

    <div class="brand">
      <span class="brand__mark"></span>
      <span class="brand__name">Kestrelbrook Student Accomodation</span>
    </div>

    <div class="person">
      <p class="person__name">Marcus Hollister</p>
      <p class="person__role">manager</p>
    </div>

    <p class="phone">
      <svg class="icon" viewBox="0 0 16 16" aria-hidden="true">
        <circle cx="8" cy="8" r="7" fill="none" stroke="var(--brand-green)" stroke-width="1.5"/>
        <path d="M5.5 4.5 l1.5 0 0.6 2 -1 0.8 c0.5 1.1 1.1 1.7 2.1 2.1 l0.8 -1 2 0.6 0 1.5 c-3.5 0.4 -6.4 -2.5 -6 -6 z" fill="var(--brand-green)"/>
      </svg>
      040 555 0142
    </p>

    <div class="contacts">
      <p class="contacts__row">
        <svg class="icon" viewBox="0 0 16 16" aria-hidden="true">
          <rect x="1" y="3" width="14" height="10" rx="1" fill="var(--brand-green)"/>
          <path d="M1.5 3.8 L8 9 L14.5 3.8" fill="none" stroke="#fff" stroke-width="1.3"/>
        </svg>
        info@kestrelbrook.com
      </p>
      <p class="contacts__row">
        <svg class="icon" viewBox="0 0 16 16" aria-hidden="true">
          <circle cx="8" cy="4.5" r="3" fill="var(--brand-green)"/>
          <path d="M2 15 c0-4 2.5-6 6-6 s6 2 6 6 z" fill="var(--brand-green)"/>
        </svg>
        kestrelbrook.com/community
      </p>
    </div>
  </section>

  <section class="card card--back" aria-label="Business card back">
    <div class="brand">
      <span class="brand__mark"></span>
      <span class="brand__name">Kestrelbrook Student Accomodation</span>
    </div>
    <p class="web">kestrelbrook.com/community</p>
  </section>

</main>
</body>
</html>
```